Where the Lantern Fades: A Sacred Wandering

This is a memoir about my breakdown/breakthrough followed by a spiritual awakening in 2012, I found my guru Harsh Omveli Dev, Mother Ayahuasca, and my spiritual mother, Ishu. By 2013, I was headed for a spiritual adventure through India, Southeast India, and Nepal which lasted 14 months. I lived in ashrams, meditated and prayed in temples,, traveled by train and bus, met many enlightened beings and interesting people. During Vipassana, I discovered my true essence- the light of my soul. It is a book of travel, romance, and spiritual growth. My idea is a road lined with temples, etc. I am walking down the road and see myself at the end of the road, facing out, with a bright star in my heart center. I see the colors in muted yellows and other earth-tone hues. Marigolds are used everywhere in the temples to adorn statues and doorways and this speaks to me. The title of the book is about finding out who I am beyond my stories and it is also about how our story will reveal to us who we really are.

Target Market(s)

Spiritual seekers, adventurers, travelers

Industry/Entity Type

Spiritual

Font styles to use
Serif
Sans Serif
Other font styles liked:
• I’m open. I like simplicity

Colors
FFC000
F8CF3A
FAE287
FDF2CF
FEFAEE

Requirements
Must have
• My name: Carla Serena Tovi, Earth tones, pastels, me or a likeness of me, room for ISBN on back cover
Nice to have
• In the photo uploads I drew an idea of what I would like, there is also the idea in the book
Should not have
• I am not a fan of bright colors and that's all I can select here. I like neutral colors, like browns, slate, creams, and whites. This reflects the dusty roads I took throughout my journey.

```html
<!DOCTYPE html>
<html lang="en">
<head>
<meta charset="utf-8">
<title>Where the Lantern Fades — Cover</title>
<link href="https://fonts.googleapis.com/css2?family=Kurale&family=Arima:wght@400;500&display=swap" rel="stylesheet">
<style>
  :root {
    --backdrop: #252525;
    --paper: #fdf6e9;
    --wash-peach: rgba(247, 212, 178, 0.55);
    --wash-sand: rgba(246, 218, 180, 0.45);
    --ink: #a39583;
  }
  * { margin: 0; padding: 0; box-sizing: border-box; }
  html, body {
    width: 1200px;
    height: 1200px;
    overflow: hidden;
    background: var(--backdrop);
  }
  .cover {
    position: absolute;
    left: 218px;
    top: 27px;
    width: 764px;
    height: 1146px;
    background:
      radial-gradient(ellipse 260px 380px at 40px 200px, var(--wash-peach), transparent 70%),
      radial-gradient(ellipse 300px 260px at 150px 560px, var(--wash-sand), transparent 70%),
      radial-gradient(ellipse 360px 300px at 680px 760px, var(--wash-peach), transparent 70%),
      radial-gradient(ellipse 420px 260px at 360px 1000px, var(--wash-sand), transparent 70%),
      radial-gradient(ellipse 300px 200px at 120px 900px, var(--wash-peach), transparent 70%),
      var(--paper);
    color: var(--ink);
    text-align: center;
  }
  .cover__title {
    position: absolute;
    top: 92px;
    left: 0;
    width: 100%;
    font-family: "Kurale", serif;
    font-weight: 400;
    font-size: 138px;
    line-height: 158px;
    text-transform: uppercase;
  }
  .cover__title span { display: block; }
  .cover__subtitle {
    position: absolute;
    top: 922px;
    left: 0;
    width: 100%;
    font-family: "Arima", serif;
    font-weight: 500;
    font-size: 54px;
    letter-spacing: 4px;
  }
  .cover__author {
    position: absolute;
    top: 1066px;
    left: 0;
    width: 100%;
    font-family: "Arima", serif;
    font-weight: 400;
    font-size: 27px;
    letter-spacing: 2px;
    text-transform: uppercase;
  }
</style>
</head>
<body>
  <main class="cover">
    <h1 class="cover__title">
      <span>Where</span>
      <span>The</span>
      <span>Lantern</span>
      <span>Fades</span>
    </h1>
    <p class="cover__subtitle">A Sacred Wandering</p>
    <p class="cover__author">Carla Serena Tovi</p>
  </main>
</body>
</html>
```